THE WELLNESS BARN WEBSITE for Physio, Fitness, health

An attractive website advertising a physiotherapyand fitness / gym business, not generic, colours are natural, greens, browns, beiges. No cheesy pictures. With the ability to sell a small,amount of goods online if i decide to. Simple to navigate. Text boxes that i can input the main information and change easily. Somewhere to put my timetable. Easy to find contact details. However many pages it needs, im not fussed.
Target Market(s)
People looking for rehabilitation or fitness classes
Industry/Entity Type
Physiotherapy, Fitness, Gym, Health
Coding
Coded - Design and coding required
Number of Pages Required
1 page
Font styles to use
Other font styles liked:
- Im not fusse,ld, not script
Requirements
Must have
- Will upload posts from my business insta page for reference about the feel. Earthy natural tones, I have a lot of timber, and rustic looking piece's, plants etc in my clinic
Nice to have
- Simple to navigate
Should not have
- Cheesy "yoga" or generic "people doing physio" pics

```html
<!DOCTYPE html>
<html lang="en">
<head>
<meta charset="utf-8">
<title>The Wellness Barn – Marlow Bay</title>
<link rel="stylesheet" href="https://fonts.googleapis.com/css2?family=Merriweather:wght@400;700&family=Open+Sans:wght@400;600;700&display=swap">
<style>
:root{
  --green:#24573a;
  --green-text:#2f6a3f;
  --brown:#8d6a3a;
  --brown-dark:#7a5a2e;
  --sage:#cddcb0;
  --sage-pale:#dde9c6;
  --ink:#1e1e1e;
  --muted:#444;
  --footer:#333333;
  --white:#ffffff;
  --serif:'Merriweather', Georgia, serif;
  --sans:'Open Sans', Arial, sans-serif;
}
*{box-sizing:border-box;margin:0;padding:0}
html,body{width:1200px;height:5021px;overflow:hidden}
body{font-family:var(--sans);color:var(--ink);background:var(--white);position:relative}
.abs{position:absolute}
section,header,footer{position:absolute;left:0;width:1200px}

/* header */
.site-header{top:0;height:117px;background:var(--white)}
.brand{left:117px;top:38px;display:flex;align-items:center;gap:10px;font-family:var(--serif);font-weight:700;font-size:20px;color:var(--green)}
.brand-dot{width:34px;height:34px;border-radius:50%;background:var(--green)}
.nav a{position:absolute;top:50px;font-size:15px;color:var(--ink);text-decoration:none}
.nav a.active{color:var(--green-text);font-weight:600;font-size:17px;top:48px}
.btn{display:inline-block;background:var(--brown);color:var(--white);border-radius:14px;text-align:center;font-weight:600;text-decoration:none}
.nav .btn-contact{position:absolute;left:949px;top:43px;width:139px;height:31px;line-height:31px;font-size:14px;color:var(--white)}

/* hero */
.hero{top:117px;height:588px;background:linear-gradient(180deg,#1b2536 0%,#27364a 30%,#2e3a30 55%,#1a2418 100%)}
.hero-copy{left:111px;top:86px;width:580px;color:var(--white)}
.hero-copy .eyebrow{font-size:20px;font-weight:600}
.hero-copy h1{font-family:var(--serif);font-size:58px;font-weight:700;margin:14px 0 16px}
.hero-copy p{font-size:20px;line-height:28px}

/* offer */
.offer{top:705px;height:710px}
.offer h2{left:111px;top:82px;font-family:var(--serif);font-size:38px;font-weight:700}
.offer .intro{left:114px;top:146px;width:980px;font-size:14px;line-height:25.5px;color:var(--ink)}
.stat-num{font-size:30px;color:var(--brown)}
.stat-label{font-size:13px;font-weight:600}
.offer .book{left:121px;top:548px;font-size:16px}
.offer .book-link{left:111px;top:586px;font-size:21px;color:var(--brown);font-weight:600}
.offer-card{top:285px;width:249px;height:347px;background:var(--sage);box-shadow:0 3px 6px rgba(0,0,0,.2)}
.offer-card .photo{height:179px}
.offer-card h3{font-family:var(--serif);font-size:17px;line-height:24px;margin:14px 11px 10px;font-weight:700}
.offer-card p{font-size:13px;line-height:21px;margin:0 11px;color:#333}

/* team */
.team{top:1415px;height:817px;background:linear-gradient(180deg,var(--green) 0 359px,var(--white) 359px)}
.team h2{left:111px;top:92px;font-family:var(--serif);font-size:34px;color:var(--white);font-weight:700}
.team .sub{left:111px;top:142px;font-size:19px;color:#e5ece4}
.team .lead{left:610px;top:88px;width:400px;font-size:20px;line-height:26px;color:#e5ece4}
.team .btn-learn{left:610px;top:160px;width:166px;height:41px;line-height:41px;font-size:19px;border-radius:8px}
.member{top:228px;width:300px;text-align:center}
.member .avatar{width:261px;height:261px;border-radius:50%;border:5px solid var(--white);box-shadow:0 0 0 2px #ccc;margin:0 auto}
.member h3{font-family:var(--serif);font-size:22px;font-weight:700;margin-top:30px}
.member .role{color:var(--brown);font-weight:700;font-size:19px;margin-top:12px}
.member p{font-size:17px;line-height:25.5px;margin-top:11px;color:#222}
.socials{display:flex;justify-content:center;gap:10px;margin-top:10px}
.socials span{width:17px;height:17px;border-radius:50%;background:var(--brown)}

/* stories */
.stories{top:2232px;height:599px;background:var(--sage-pale)}
.stories h2{width:100%;text-align:center;top:78px;font-family:var(--serif);font-size:36px;font-weight:700}
.stories .sub{width:100%;text-align:center;top:138px;font-size:20px}
.review{top:249px;width:312px;height:271px;background:var(--white);border-radius:6px;box-shadow:0 3px 6px rgba(0,0,0,.25);padding:44px 20px 0}
.review-avatar{top:-45px;width:78px;height:78px;border-radius:50%;border:3px solid var(--white)}
.review .gmark{position:absolute;right:22px;top:62px;width:34px;height:34px;border-radius:50%;background:#c9c9c9}
.review h4{font-family:var(--serif);font-size:17px;font-weight:700;margin-top:17px}
.review .who{font-size:13px;margin-top:6px}
.review .stars{color:#f2a51a;font-size:17px;letter-spacing:1px;margin-top:3px}
.review p{font-size:13.5px;line-height:19px;margin-top:8px}
.review .more{font-size:15px;color:var(--brown);font-weight:600;margin-top:20px;display:block}

/* products */
.products{top:2831px;height:580px}
.products h2{width:100%;text-align:center;top:82px;font-family:var(--serif);font-size:36px;font-weight:700}
.product{top:161px;width:240px;text-align:center}
.product .photo{width:220px;height:220px;border-radius:50%;margin:0 auto;box-shadow:0 5px 0 #3b6fa0}
.product h3{font-family:var(--serif);font-size:21px;color:var(--green-text);font-weight:700;margin-top:24px}
.product .price{font-size:17px;margin-top:14px}
.product .shop{font-size:17px;font-weight:600;margin-top:14px}

/* contact */
.contact{top:3411px;height:692px;background:linear-gradient(180deg,#5d4e36 0%,#584a33 45%,#4c4530 75%,#403a28 100%)}
.contact h2{width:100%;text-align:center;top:80px;font-family:var(--serif);font-size:36px;color:var(--white);font-weight:700}
.contact .sub{width:100%;text-align:center;top:138px;font-size:20px;color:#eee}
.info{left:111px;width:480px;color:var(--white)}
.info .icon{position:absolute;left:0;top:0;width:42px;height:42px;border-radius:50%;background:var(--white);display:flex;align-items:center;justify-content:center}
.info small{position:absolute;left:64px;top:-6px;width:400px;font-size:13px;line-height:29px;color:#eee}
.info .big{position:absolute;left:64px;font-size:21px;line-height:30px}
.form-card{left:653px;top:214px;width:435px;height:394px;background:var(--white);border-radius:6px;padding:32px 41px}
.form-card h3{font-family:var(--serif);font-size:20px;font-weight:700}
.field{border-bottom:1px solid #777;height:28px;font-size:15px;color:#555;margin-top:30px;width:316px}
.field:first-of-type{margin-top:28px}
.btn-submit{margin-top:35px;width:125px;height:37px;line-height:37px;font-size:19px;border-radius:6px}

/* faq */
.faq{top:4103px;height:512px}
.faq h2{left:111px;top:92px;font-family:var(--serif);font-size:36px;line-height:46px;font-weight:700}
.faq h2 span{color:var(--brown)}
.faq .intro{left:114px;top:200px;width:390px;font-size:13.5px;line-height:25px}
.faq .banner{left:111px;top:292px;width:369px;height:166px;background:linear-gradient(90deg,#111 0%,#1c1c1c 100%)}
.faq-list{left:553px;top:108px;width:432px}
.faq-item{border-bottom:1px solid #888;position:relative}
.faq-item h4{font-size:15.5px;font-weight:600;padding:0 0 0 3px}
.faq-item .toggle{position:absolute;right:-62px;top:0;font-size:20px;color:#666}
.faq-item p{font-size:13.5px;line-height:25px;margin-top:10px;padding-bottom:18px;color:#333}
.faq .still{left:553px;top:437px;font-size:16px;color:var(--brown);font-weight:700}

/* footer */
.site-footer{top:4615px;height:406px;background:var(--footer);color:var(--white)}
.foot-brand{left:112px;top:90px;font-family:var(--serif);font-weight:700;font-size:18px;width:240px;line-height:24px}
.foot-about{left:114px;top:195px;width:260px;font-size:13px;line-height:18px}
.foot-col{top:80px}
.foot-col h5{font-size:20px;font-weight:400}
.foot-col ul{list-style:none;margin-top:16px}
.foot-col li{font-size:13px;height:37px}
.foot-col li::before{content:"»";margin-right:8px}
.help li{display:flex;gap:14px;font-size:13.5px;line-height:25px;height:auto;margin-bottom:20px}
.help li::before{content:none}
.foot-rule{left:111px;top:313px;width:972px;height:1px;background:#999}
.copy{width:100%;text-align:center;top:342px;font-size:13.5px}
</style>
</head>
<body>

<header class="site-header">
  <div class="brand abs"><span class="brand-dot"></span>The Wellness Barn</div>
  <nav class="nav">
    <a href="#" class="active" style="left:423px">Home</a>
    <a href="#" style="left:513px">About</a>
    <a href="#" style="left:601px">Why Choose Us</a>
    <a href="#" style="left:760px">Services</a>
    <a href="#" style="left:867px">Blog</a>
    <a href="#" class="btn btn-contact">Contact Us</a>
  </nav>
</header>

<section class="hero" role="img" aria-label="Group of clinic members in matching black tops standing arm in arm on a sports field at dusk">
  <div class="hero-copy abs">
    <div class="eyebrow">Welcome to The Wellness Barn</div>
    <h1>Marlow Bay</h1>
    <p>Discover a healthier you with our Physiotherapist led programs. At The Wellness Barn Marlow Bay, we focus on safe and effective movement to enhance your quality of life. Join us for a comprehensive approach to wellbeing.</p>
  </div>
</section>

<section class="offer">
  <h2 class="abs">What do we have to offer?</h2>
  <p class="intro abs">The Wellness Barn Marlow Bay is dedicated to empowering individuals to achieve their health and wellbeing goals through safe and effective movement. Our core values include Integrity, Collaboration, Inclusivity, and a strong Commitment to health. We believe in providing professional support tailored to each individual's needs. Our team, including experienced professionals like Dr. Clara Whitfield and Tom Redding, is committed to guiding you on your wellness journey. Join us in fostering a healthier community where everyone can thrive.</p>
  <div class="abs stat-num" style="left:133px;top:290px">10+</div>
  <div class="abs stat-label" style="left:115px;top:347px">Yoga Coaches</div>
  <div class="abs stat-num" style="left:133px;top:413px">8k+</div>
  <div class="abs stat-label" style="left:115px;top:469px">Happy Clients</div>
  <div class="abs book">Book Now</div>
  <div class="abs book-link">Book Your Class</div>

  <article class="offer-card abs" style="left:308px">
    <div class="photo" role="img" aria-label="Group class using exercise balls in a bright studio" style="background:linear-gradient(180deg,#c9d4dc,#8aa3b6 60%,#5f7f95)"></div>
    <h3>Physiotherapy Classes for Everyone</h3>
    <p>Our Classes are tailored for all ages, focusing on safe movement to enhance mobility and overall health.</p>
  </article>
  <article class="offer-card abs" style="left:573px">
    <div class="photo" role="img" aria-label="Practitioner preparing a healthy green drink in a kitchen" style="background:linear-gradient(180deg,#f1f1ee,#dcdcd4 60%,#b9c4a6)"></div>
    <h3>Holistic Welllness Programs</h3>
    <p>Our Programs integrate physical activity with nutritional guidance to support health improvements.</p>
  </article>
  <article class="offer-card abs" style="left:840px">
    <div class="photo" role="img" aria-label="Person meditating on a beach at sunset" style="background:linear-gradient(180deg,#6f8fb0,#e3b98a 55%,#c99460 80%,#8a6a4a)"></div>
    <h3>Mindfulness and Yoga Sessions</h3>
    <p>Join our yoga sessions to improve mental clarity and physical flexibility in a calming environment.</p>
  </article>
</section>

<section class="team">
  <h2 class="abs">Meet Our Team</h2>
  <div class="abs sub">Get to Know Us</div>
  <p class="abs lead">Discover the dedicated professionals committed to your health.</p>
  <a href="#" class="btn btn-learn abs">Learn More</a>

  <div class="member abs" style="left:107px">
    <div class="avatar" role="img" aria-label="Portrait of the lead physiotherapist in a clinic" style="background:linear-gradient(180deg,#ece6dc,#cfc3b1)"></div>
    <h3>Dr. Clara Whitfield</h3>
    <div class="role">Lead Physiotherapist</div>
    <p>Dr. Clara specializes in sports rehabilitation and has over 10 years of experience in helping clients recover from injuries.</p>
    <div class="socials"><span></span><span></span><span></span><span></span></div>
  </div>
  <div class="member abs" style="left:450px">
    <div class="avatar" role="img" aria-label="Portrait of the wellness coach in a library" style="background:linear-gradient(180deg,#6a5643,#3b3129)"></div>
    <h3>Daniel Okoro</h3>
    <div class="role">Wellness Coach</div>
    <p>Daniel focuses on holistic health and wellness, guiding clients through lifestyle changes to improve their overall wellbeing.</p>
    <div class="socials"><span></span><span></span><span></span><span></span></div>
  </div>
  <div class="member abs" style="left:791px">
    <div class="avatar" role="img" aria-label="Portrait of the physiotherapy assistant in blue scrubs" style="background:linear-gradient(180deg,#d9c9b0,#5d7fa8)"></div>
    <h3>Lily Tran</h3>
    <div class="role">Physiotherapy Assistant</div>
    <p>Lily assists in physiotherapy sessions and is passionate about helping clients achieve their health goals.</p>
    <div class="socials"><span></span><span></span><span></span><span></span></div>
  </div>
</section>

<section class="stories">
  <h2 class="abs">Client Success Stories</h2>
  <div class="abs sub">Hear from our clients about their transformative journeys with us.</div>

  <article class="review abs" style="left:111px">
    <div class="review-avatar abs" role="img" aria-label="Client portrait" style="left:117px;background:#a8745a"></div>
    <span class="gmark"></span>
    <h4>Rachel Moore</h4>
    <div class="who">Fitness Enthusiast</div>
    <div class="stars">★★★★★</div>
    <p>The Wellness Barn has completely changed my approach to fitness. Their programs are tailored and effective!</p>
    <a class="more">Read More</a>
  </article>
  <article class="review abs" style="left:444px">
    <div class="review-avatar abs" role="img" aria-label="Client portrait" style="left:117px;background:#b8957a"></div>
    <span class="gmark"></span>
    <h4>Peter Lawson</h4>
    <div class="who">Retired Veteran</div>
    <div class="stars">★★★★★</div>
    <p>I never thought I could regain my mobility. The physiotherapy classes here are a game changer!</p>
    <a class="more">Read More</a>
  </article>
  <article class="review abs" style="left:777px">
    <div class="review-avatar abs" role="img" aria-label="Client portrait" style="left:117px;background:#9c6a4e"></div>
    <span class="gmark"></span>
    <h4>Hannah Price</h4>
    <div class="who">Busy Mom</div>
    <div class="stars">★★★★★</div>
    <p>I love how the wellness programs fit into my hectic schedule. I feel healthier and more energetic!</p>
    <a class="more">Read More</a>
  </article>
</section>

<section class="products">
  <h2 class="abs">Our Products</h2>
  <div class="product abs" style="left:106px">
    <div class="photo" role="img" aria-label="Amber bottle of body oil among green leaves" style="background:radial-gradient(circle,#6d6a5a,#3f5a33)"></div>
    <h3>Fern Body</h3><div class="price">Price :&nbsp; $ 25</div><div class="shop">Shop Now</div>
  </div>
  <div class="product abs" style="left:357px">
    <div class="photo" role="img" aria-label="Branded drink cooler" style="background:radial-gradient(circle,#8a4a52,#6b6b6b)"></div>
    <h3>Wellness Barn</h3><div class="price" style="margin-top:20px">Price :&nbsp; $ 23</div><div class="shop">Shop Now</div>
  </div>
  <div class="product abs" style="left:609px">
    <div class="photo" role="img" aria-label="Heat packs in fabric covers" style="background:radial-gradient(circle,#c0784a,#b9a58d)"></div>
    <h3>Wheat Bags</h3><div class="price" style="margin-top:26px">Price :&nbsp; $ 32</div><div class="shop">Shop Now</div>
  </div>
  <div class="product abs" style="left:858px">
    <div class="photo" role="img" aria-label="Green cap and grey shirt" style="background:radial-gradient(circle,#3c4a3a,#b7b9b6)"></div>
    <h3>Snap Back</h3><div class="price" style="margin-top:26px">Price :&nbsp; $ 30</div><div class="shop">Shop Now</div>
  </div>
</section>

<section class="contact" role="img" aria-label="Team standing arm in arm on a sports field behind a warm brown overlay">
  <h2 class="abs">Contact Us</h2>
  <div class="abs sub">Hear from our clients about their transformative journeys with us.</div>

  <div class="info abs" style="top:222px">
    <span class="icon"><svg width="22" height="22" viewBox="0 0 24 24"><path d="M12 2a7 7 0 0 0-7 7c0 5 7 13 7 13s7-8 7-13a7 7 0 0 0-7-7z" fill="none" stroke="#8d6a3a" stroke-width="2.2"/><circle cx="12" cy="9" r="2.6" fill="#8d6a3a"/></svg></span>
    <small>Come visit us to learn more about our programs and how we can help you achieve your health goals.</small>
    <div class="big" style="top:70px">45 Timber Lane, Marlow Bay,<br>Australia, 4700.</div>
  </div>
  <div class="info abs" style="top:370px">
    <span class="icon"><svg width="22" height="22" viewBox="0 0 24 24"><path d="M6.6 10.8a15 15 0 0 0 6.6 6.6l2.2-2.2a1 1 0 0 1 1-.25 11 11 0 0 0 3.6.6 1 1 0 0 1 1 1V20a1 1 0 0 1-1 1A17 17 0 0 1 3 4a1 1 0 0 1 1-1h3.5a1 1 0 0 1 1 1 11 11 0 0 0 .6 3.6 1 1 0 0 1-.25 1z" fill="#8d6a3a"/></svg></span>
    <small>Our team is available to take your calls and provide support during business hours.</small>
    <div class="big" style="top:80px;left:68px">+61 7 4000 2468.</div>
  </div>
  <div class="info abs" style="top:510px">
    <span class="icon"><svg width="22" height="22" viewBox="0 0 24 24"><rect x="3" y="5" width="18" height="14" rx="1.5" fill="none" stroke="#8d6a3a" stroke-width="2"/><path d="M3 6l9 7 9-7" fill="none" stroke="#8d6a3a" stroke-width="2"/></svg></span>
    <small>For inquiries or more information, feel free to reach out via email at</small>
    <div class="big" style="top:66px">hello@wellnessbarnmarlow.com</div>
  </div>

  <form class="form-card abs">
    <h3>Send Message</h3>
    <div class="field">Name</div>
    <div class="field">Email</div>
    <div class="field">Enter your message...</div>
    <div class="btn btn-submit">Submit</div>
  </form>
</section>

<section class="faq">
  <h2 class="abs">Frequently Asked<br>Questions <span>(FAQs)</span></h2>
  <p class="intro abs">Find answers to common questions about our health and wellness programs, services, and how we can support your journey to better health.</p>
  <div class="banner abs" role="img" aria-label="Partner fitness banner in black and green"></div>
  <div class="faq-list abs">
    <div class="faq-item">
      <h4>What types of programs do you offer?</h4><span class="toggle">–</span>
      <p>We offer a variety of programs including physiotherapy classes, wellness programs, and tailored fitness plans designed for all ages and abilities.</p>
    </div>
    <div class="faq-item" style="padding:28px 0 14px">
      <h4>How to Use the Weight Loss Bundle?</h4><span class="toggle" style="top:24px">+</span>
    </div>
    <div class="faq-item" style="padding:28px 0 14px">
      <h4>What are the side effects Root Cleanse since it's a detox?</h4><span class="toggle" style="top:24px">+</span>
    </div>
  </div>
  <div class="still abs">Still have questions? Contact us at Marlowbay.com</div>
</section>

<footer class="site-footer">
  <div class="foot-brand abs">The Wellness Barn</div>
  <p class="foot-about abs">Discover a healthier you with our Physiotherapist led programs. At The Wellness Barn Marlow Bay, we focus on safe and effective movement to enhance your quality of life.</p>
  <div class="foot-col abs" style="left:432px">
    <h5>Our Services</h5>
    <ul><li>Physiotherapy</li><li>Holistic Wellness</li><li>Yoga Session</li><li>Mindfulness</li><li>Nutrition Guidance</li></ul>
  </div>
  <div class="foot-col abs" style="left:663px">
    <h5>Company</h5>
    <ul><li>About Us</li><li>Services</li><li>Blog</li><li>Why Choose Us</li><li>Contact</li></ul>
  </div>
  <div class="foot-col help abs" style="left:863px">
    <h5>Get Help</h5>
    <ul>
      <li><svg width="20" height="20" viewBox="0 0 24 24"><path d="M6.6 10.8a15 15 0 0 0 6.6 6.6l2.2-2.2a1 1 0 0 1 1-.25 11 11 0 0 0 3.6.6 1 1 0 0 1 1 1V20a1 1 0 0 1-1 1A17 17 0 0 1 3 4a1 1 0 0 1 1-1h3.5a1 1 0 0 1 1 1 11 11 0 0 0 .6 3.6 1 1 0 0 1-.25 1z" fill="#fff"/></svg>+61 7 4000 2468</li>
      <li><svg width="20" height="20" viewBox="0 0 24 24"><rect x="3" y="5" width="18" height="14" rx="1.5" fill="none" stroke="#fff" stroke-width="2"/><path d="M3 6l9 7 9-7" fill="none" stroke="#fff" stroke-width="2"/></svg>hello@wellnessbarnmarlow.com</li>
      <li><svg width="20" height="20" viewBox="0 0 24 24"><path d="M12 2a7 7 0 0 0-7 7c0 5 7 13 7 13s7-8 7-13a7 7 0 0 0-7-7z" fill="#fff"/><circle cx="12" cy="9" r="2.6" fill="#333"/></svg>45 Timber Lane, Marlow Bay,<br>Australia, 4700.</li>
    </ul>
  </div>
  <div class="foot-rule abs"></div>
  <div class="copy abs">Copyright © 2025.hello@wellnessbarnmarlow.com. All Rights Reserved.</div>
</footer>

</body>
</html>
```